Ward Compass Business Card Design*

We need a business card design for our company Ward Compass. Our company is specialized in providing online consulting services regarding medical institutions, hospitals and doctors. We work with patients worldwide looking to choose between healthcare providers. We have a website you may use as a reference, where we list doctors and clinics worldwide. So we target Medical providers as well as patients worldwide.
Target Market(s)
Medical Providers and patients around the world
Industry/Entity Type
Medical
Contact Information for Business Card
Salwa Kettani
CEO
+90 612 348 2175
info@wardcompass.example
www.wardcompass.example
14 Annakhil 7 H.R.B. Rabat, Morocco
Requirements
Must have
- Company logo/name on one full side, personal info and smaller logo and company name on the other side.
Nice to have
- Smart and elegant design

```html
<!DOCTYPE html>
<html lang="en">
<head>
<meta charset="utf-8">
<title>Ward Compass — Business Card</title>
<link rel="stylesheet" href="https://fonts.googleapis.com/css2?family=Montserrat:wght@400;600;700&family=Open+Sans:wght@400;600&display=swap">
<style>
  :root {
    --navy: #143764;
    --white: #ffffff;
    --grey: #7f7f7f;
    --backdrop: #3a3d44;
    --card-w: 700px;
    --card-h: 400px;
  }
  * { box-sizing: border-box; margin: 0; padding: 0; }
  html, body { width: 1200px; height: 1000px; overflow: hidden; }
  body {
    background: var(--backdrop);
    font-family: "Open Sans", Arial, sans-serif;
    position: relative;
  }
  .card {
    position: absolute;
    left: 250px;
    width: var(--card-w);
    height: var(--card-h);
    border-radius: 22px;
    overflow: hidden;
    box-shadow: 0 14px 30px rgba(0,0,0,.35);
  }
  .card--back { top: 60px; background: var(--navy); display: flex; align-items: center; justify-content: center; }
  .card--front { top: 540px; background: var(--navy); }

  .brand { display: flex; align-items: center; gap: 14px; }
  .brand__dot { width: 34px; height: 34px; border-radius: 50%; flex: none; }
  .brand__name { font-family: "Montserrat", Arial, sans-serif; font-weight: 600; white-space: nowrap; }
  .card--back .brand__dot { background: var(--white); width: 56px; height: 56px; }
  .card--back .brand__name { color: var(--white); font-size: 46px; letter-spacing: 1px; }

  .front__shape { position: absolute; inset: 0; }
  .card--front .brand { position: absolute; left: 40px; top: 152px; gap: 12px; }
  .card--front .brand__dot { background: var(--navy); width: 30px; height: 30px; }
  .card--front .brand__name { color: var(--navy); font-size: 26px; letter-spacing: .5px; }

  .holder { position: absolute; right: 40px; top: 48px; text-align: right; color: var(--white); font-family: "Montserrat", Arial, sans-serif; font-weight: 700; white-space: nowrap; }
  .holder__name { font-size: 22px; letter-spacing: 1px; text-transform: uppercase; }
  .holder__role { font-size: 18px; margin-top: 6px; }

  .address { position: absolute; right: 40px; top: 208px; text-align: right; color: var(--navy); font-size: 16px; line-height: 1.3; white-space: nowrap; }

  .contacts { position: absolute; right: 40px; top: 290px; list-style: none; color: var(--white); font-size: 16px; line-height: 1.65; text-align: right; white-space: nowrap; }
  .contacts li { display: flex; align-items: center; justify-content: flex-end; gap: 10px; }
  .contacts svg { width: 14px; height: 14px; fill: var(--white); flex: none; }
</style>
</head>
<body>

<section class="card card--back" aria-label="Card back">
  <div class="brand">
    <span class="brand__dot"></span>
    <span class="brand__name">Ward Compass</span>
  </div>
</section>

<section class="card card--front" aria-label="Card front">
  <svg class="front__shape" viewBox="0 0 700 400" preserveAspectRatio="none" aria-hidden="true">
    <circle cx="20" cy="20" r="350" fill="#ffffff"/>
    <rect x="300" y="196" width="400" height="66" fill="#ffffff"/>
  </svg>

  <div class="brand">
    <span class="brand__dot"></span>
    <span class="brand__name">Ward Compass</span>
  </div>

  <div class="holder">
    <p class="holder__name">Salwa Kettani</p>
    <p class="holder__role">CEO</p>
  </div>

  <p class="address">14 Annakhil 7 H.R.B.<br>Rabat, Morocco</p>

  <ul class="contacts">
    <li>+90 612 348 2175
      <svg viewBox="0 0 24 24"><path d="M6.6 10.8a15 15 0 0 0 6.6 6.6l2.2-2.2a1 1 0 0 1 1-.25 11.4 11.4 0 0 0 3.6.57 1 1 0 0 1 1 1V20a1 1 0 0 1-1 1A17 17 0 0 1 3 4a1 1 0 0 1 1-1h3.5a1 1 0 0 1 1 1c0 1.25.2 2.45.57 3.57a1 1 0 0 1-.25 1z"/></svg>
    </li>
    <li>info@wardcompass.example
      <svg viewBox="0 0 24 24"><path d="M3 5h18v14H3zm2 2v.5l7 5 7-5V7zm0 3v7h14v-7l-7 5z"/></svg>
    </li>
    <li>www.wardcompass.example
      <svg viewBox="0 0 24 24"><path d="M12 2a10 10 0 1 0 0 20 10 10 0 0 0 0-20zm0 2c.9 0 2.2 2 2.7 5H9.3C9.8 6 11.1 4 12 4zM4.3 11h4.8a19 19 0 0 0 0 2H4.3a8 8 0 0 1 0-2zm10.6 0h4.8a8 8 0 0 1 0 2h-4.8a19 19 0 0 0 0-2zM9.3 15h5.4c-.5 3-1.8 5-2.7 5s-2.2-2-2.7-5z"/></svg>
    </li>
  </ul>
</section>

</body>
</html>
```